Website Landing Page Kestrel Plumbing

Dear Contestants,

I would like you to design me a landing page for my new website. I have attached a screen shot of my current website which is being constructed.

I do not want the lay out to change at all as my web designer has put this system together and the layout cannot change.

-I would like a designer to come up with something creative and appealing. I would like the website to be classy and elegant.

-I have also attached my flyer design etc so you get an idea of colours etc.

Also I have files etc of logo etc and photos if you would like me to email them that is no issue.

I am happy to provide more info if you request at anytime.

If anyone needs files I can email photos etc. Please reach out.

Industry/Entity Type

Plumbing

```html
<!DOCTYPE html>
<html lang="en">
<head>
<meta charset="utf-8">
<title>Kestrel Plumbing</title>
<link rel="stylesheet" href="https://fonts.googleapis.com/css2?family=Oswald:wght@300;400&family=Roboto:wght@300;400;700;900&family=Roboto+Condensed:wght@700&display=swap">
<style>
:root{
  --sky:#07a7d3;
  --sky-soft:#2aabd9;
  --nav:#565656;
  --nav-line:#6a6a6a;
  --white:#ffffff;
  --ink:#111111;
  --accent:#0aa3d6;
}
*{margin:0;padding:0;box-sizing:border-box}
html,body{width:1200px;height:762px;overflow:hidden}
body{background:var(--sky);font-family:'Roboto',sans-serif;color:var(--white);position:relative}

.top-phone{position:absolute;left:126px;top:12px;font-weight:700;font-size:14px}
.brand{position:absolute;left:457px;top:13px;width:250px;height:117px;background:var(--sky-soft);display:flex;flex-direction:column;align-items:center;justify-content:center}
.brand-mark{width:22px;height:22px;border-radius:50%;background:var(--ink);margin-bottom:10px}
.brand-name{font-family:'Roboto Condensed',sans-serif;font-weight:700;font-size:23px;color:var(--ink);line-height:1}

.social{position:absolute;left:976px;top:8px;display:flex;gap:2px}
.social span{width:19px;height:19px;border-radius:50%;background:var(--white);border:2px solid #2d5c9a}

.main-nav{position:absolute;left:0;top:134px;width:1200px;height:49px;background:var(--nav);border-bottom:1px solid #8fd3ea}
.main-nav ul{list-style:none;position:absolute;left:153px;top:0;height:49px;display:flex;border-left:1px solid var(--nav-line)}
.main-nav li{height:49px;display:flex;align-items:center;justify-content:center;border-right:1px solid var(--nav-line);font-family:'Roboto',sans-serif;font-weight:700;font-size:13px;color:var(--white);letter-spacing:-0.2px}
.main-nav .caret{font-size:9px;margin-left:4px}

.promo{position:absolute;top:198px;width:321px;height:300px;background:var(--white);padding:20px 18px}
.promo-art{position:relative;width:283px;height:260px;overflow:hidden;font-family:'Oswald',sans-serif;font-weight:300;text-align:center}
.estimate{background:linear-gradient(180deg,#6bbcc0 0%,#4aa3ad 55%,#2f7f8c 100%)}
.estimate h2{position:absolute;top:36px;left:0;width:100%;font-weight:300;font-size:42px;line-height:42px}
.estimate .cta{position:absolute;left:85px;top:188px;width:117px;height:31px;background:var(--white);color:#2c8d98;font-size:16px;line-height:31px}

.launch .photo{position:absolute;left:0;top:0;width:100%;height:188px;background:linear-gradient(180deg,#6b7a6a 0%,#9aa7b8 55%,#b9c3d3 100%)}
.launch .band{position:absolute;left:0;top:188px;width:100%;height:72px;background:var(--accent)}
.launch .big{position:absolute;top:124px;left:0;width:100%;font-size:56px;line-height:1;color:var(--accent);font-weight:400}
.launch .label{position:absolute;top:187px;left:0;width:100%;font-size:34px;line-height:1.1}
.launch .date{position:absolute;top:227px;left:0;width:100%;font-size:14px}

.newyear{background:radial-gradient(ellipse at 50% 55%,#2a8ea6 0%,#1a6c80 55%,#0f4e62 100%)}
.newyear .bunting{position:absolute;left:0;top:0;width:100%;height:78px;background:linear-gradient(90deg,#5fbf6a,#e8c63a,#e0457c,#4fc0e0,#e25b3c,#7bd05b)}
.newyear .big{position:absolute;top:108px;left:0;width:100%;font-size:56px;line-height:1;font-weight:400}
.newyear .label{position:absolute;top:168px;left:0;width:100%;font-size:33px;line-height:1.1}
.newyear .date{position:absolute;top:230px;left:0;width:100%;font-size:14px}

.intro{position:absolute;left:0;top:516px;width:1180px;text-align:center}
.intro h1{font-size:43px;font-weight:300;line-height:56px}
.intro h1 strong{font-weight:900}
.intro p{font-weight:300;font-size:20.5px;line-height:24px}
.intro .lead{margin-top:11px}
.intro .more{margin-top:17px}
.about-btn{display:inline-block;margin-top:16px;width:150px;height:35px;border-radius:6px;background:var(--white);color:var(--accent);font-size:21px;line-height:35px}
</style>
</head>
<body>
<header>
  <div class="top-phone">Phone: 0413572968</div>
  <div class="brand">
    <span class="brand-mark"></span>
    <span class="brand-name">KESTREL PLUMBING</span>
  </div>
  <div class="social" aria-label="Social links"><span></span><span></span><span></span><span></span><span></span></div>
  <nav class="main-nav">
    <ul>
      <li style="width:86px">HOME</li>
      <li style="width:131px">EMERGENCY<span class="caret">▼</span></li>
      <li style="width:116px">HOT WATER<span class="caret">▼</span></li>
      <li style="width:102px">LEAKING<span class="caret">▼</span></li>
      <li style="width:102px">BLOCKED<span class="caret">▼</span></li>
      <li style="width:120px">BATHROOM<span class="caret">▼</span></li>
      <li style="width:139px">OTHER SERVICES</li>
      <li style="width:41px"><svg width="11" height="11" viewBox="0 0 11 11"><circle cx="4.5" cy="4.5" r="3.2" fill="none" stroke="#fff" stroke-width="1.8"/><line x1="7" y1="7" x2="10" y2="10" stroke="#fff" stroke-width="2"/></svg></li>
    </ul>
  </nav>
</header>

<section class="promo" style="left:117px">
  <div class="promo-art estimate" role="img" aria-label="Photo of hands using a calculator over paperwork">
    <h2>Receive a Free<br>Estimate</h2>
    <div class="cta">CLICK HERE</div>
  </div>
</section>

<section class="promo" style="left:441px">
  <div class="promo-art launch">
    <div class="photo" role="img" aria-label="Photo of the two plumbers outdoors"></div>
    <div class="band"></div>
    <div class="big">20%OFF</div>
    <div class="label">website launch sale</div>
    <div class="date">February 18, 2016</div>
  </div>
</section>

<section class="promo" style="left:765px">
  <div class="promo-art newyear">
    <div class="bunting" role="img" aria-label="Colourful party bunting and confetti"></div>
    <div class="big">20%OFF</div>
    <div class="label">new year sale</div>
    <div class="date">January 1, 2016</div>
  </div>
</section>

<section class="intro">
  <h1>Rwice the quality. <strong>Twice the care.</strong></h1>
  <p class="lead">with over 20 years of experience servicing Sydney homes and businesses<br>the Kestrel Plumbers are some of the best in the business.</p>
  <p class="more">Click below to find out more ablut us.</p>
  <a class="about-btn">ABOUT US</a>
</section>
</body>
</html>
```